Business Cards Needed for Innovative Healthcare Marketing Company

We are a marketing company focused on healthcare. Our company is all about rebranding yourself renewing your image and generating results. The phoenix stands for "reborn" or "rising" which we provide new brands for our clients we take their old brands and renew it with creativity and innovation. I am looking for a business card with color dimension. I have attached an example of a card I think has the look and feel of what I am trying to accomplish. I like that the card example has black and grey font colors, I like the font placement and the small logo, I really like the use of the colors on the right those are the colors of my logo. My logo is phoenix so maybe incorporating flames similar to that design. I would like the back a solid color maybe red with an opaque version of the logo and website. As a marketing company I am always open to creative liberty!

Target Market(s)

Doctors and business professionals.

Industry/Entity Type

Marketing

Contact Information for Business Card

Valcorne Health Care Marketing
Marla Tenwick- CEO
#(512)638-2974
email-marla@valcorne.com
website- valcorne.com

Font styles to use
Sans Serif

Colors
ec1f27
f37122
ffc214
fbed22
fbf289
f04a50

Requirements
Must have
• The logo and required information
Nice to have
• icons by the information
Should not have
• child like font

```html
<!DOCTYPE html>
<html lang="en">
<head>
<meta charset="utf-8">
<title>Valcorne Health Care Marketing – Business Card</title>
<link rel="stylesheet" href="https://fonts.googleapis.com/css2?family=Josefin+Sans:wght@300&family=Open+Sans:wght@400;600&display=swap">
<style>
  :root {
    --stage: #eceae7;
    --card-white: #ffffff;
    --flame-orange: #f08a1f;
    --flame-mid: #d4481f;
    --flame-red: #a41c22;
    --brand-red: #9b1b1f;
    --ink-light: #ffffff;
    --illus-light: #fbe3c4;
    --illus-orange: #f37122;
    --illus-red: #c0301f;
    --mark-tone: #e0602a;
    --faint-grey: #ececec;
  }
  * { box-sizing: border-box; margin: 0; padding: 0; }
  html, body { width: 1200px; height: 900px; overflow: hidden; }
  body {
    background: var(--stage);
    position: relative;
    font-family: "Open Sans", Arial, sans-serif;
  }
  .card {
    position: absolute;
    width: 556px;
    height: 343px;
    overflow: hidden;
    box-shadow: 0 4px 14px rgba(0,0,0,0.18);
  }
  /* Front */
  .card-front {
    left: 237px; top: 62px;
    background: linear-gradient(180deg, var(--flame-orange) 0%, var(--flame-mid) 48%, var(--flame-red) 78%, var(--flame-red) 100%);
  }
  .front-illustration {
    position: absolute;
    left: 0; top: 0;
    width: 240px; height: 343px;
  }
  .brand-block {
    position: absolute;
    right: 41px; top: 54px;
    text-align: right;
    font-family: "Josefin Sans", "Open Sans", sans-serif;
    font-weight: 300;
    color: var(--ink-light);
  }
  .brand-name { font-size: 40px; letter-spacing: 1px; line-height: 1; }
  .brand-rule { height: 1px; background: currentColor; opacity: 0.7; margin-top: 6px; }
  .brand-tag { font-size: 14px; letter-spacing: 1px; margin-top: 6px; text-transform: uppercase; }
  .person {
    position: absolute;
    right: 37px; top: 152px;
    text-align: right;
    color: var(--ink-light);
  }
  .person-name { font-size: 20px; font-weight: 600; line-height: 1.2; }
  .person-role { font-size: 15px; font-weight: 400; margin-top: 5px; }
  .contact-list {
    position: absolute;
    right: 36px; top: 238px;
    list-style: none;
    color: var(--ink-light);
    font-size: 16px;
  }
  .contact-item {
    display: flex;
    justify-content: flex-end;
    align-items: center;
    gap: 10px;
    height: 23px;
  }
  .contact-icon { width: 13px; height: 13px; flex: none; }
  /* Back */
  .card-back {
    left: 457px; top: 518px;
    width: 560px; height: 344px;
    background: var(--card-white);
  }
  .back-decoration {
    position: absolute;
    left: 323px; top: 0;
    width: 237px; height: 344px;
    background: linear-gradient(160deg, var(--faint-grey) 0%, #f3f3f3 55%, var(--faint-grey) 100%);
  }
  .back-mark {
    position: absolute;
    left: 84px; top: 50px;
    width: 140px; height: 140px;
    border-radius: 50%;
    background: var(--mark-tone);
  }
  .back-brand {
    position: absolute;
    left: 43px; top: 226px;
    font-family: "Josefin Sans", "Open Sans", sans-serif;
    font-weight: 300;
    color: var(--brand-red);
  }
  .back-brand .brand-name { font-size: 46px; letter-spacing: 1px; }
  .back-brand .brand-rule { margin-top: 6px; }
  .back-brand .brand-tag { font-size: 15px; margin-top: 6px; }
</style>
</head>
<body>

<section class="card card-front">
  <svg class="front-illustration" viewBox="0 0 240 343" role="img" aria-label="Phoenix illustration with outstretched flame-coloured wings">
    <defs>
      <linearGradient id="illusFill" x1="0" y1="0" x2="0" y2="1">
        <stop offset="0" stop-color="var(--illus-red)"/>
        <stop offset="0.5" stop-color="var(--illus-orange)"/>
        <stop offset="1" stop-color="#f5a02a"/>
      </linearGradient>
      <linearGradient id="illusBase" x1="0" y1="0" x2="1" y2="0">
        <stop offset="0" stop-color="var(--card-white)"/>
        <stop offset="1" stop-color="var(--illus-light)"/>
      </linearGradient>
    </defs>
    <rect width="240" height="343" fill="url(#illusBase)"/>
    <rect width="240" height="343" fill="url(#illusFill)" opacity="0.55"/>
  </svg>

  <div class="brand-block">
    <div class="brand-name">VALCORNE</div>
    <div class="brand-rule"></div>
    <div class="brand-tag">Health Care Marketing</div>
  </div>

  <div class="person">
    <div class="person-name">Marla Tenwick</div>
    <div class="person-role">CEO</div>
  </div>

  <ul class="contact-list">
    <li class="contact-item">
      <span>(512)638-2974</span>
      <svg class="contact-icon" viewBox="0 0 24 24" aria-hidden="true"><path fill="#fff" d="M6.6 10.8a15.1 15.1 0 0 0 6.6 6.6l2.2-2.2c.3-.3.7-.4 1-.2 1.1.4 2.3.6 3.6.6.6 0 1 .4 1 1V20c0 .6-.4 1-1 1A17 17 0 0 1 3 4c0-.6.4-1 1-1h3.5c.6 0 1 .4 1 1 0 1.3.2 2.5.6 3.6.1.3 0 .7-.2 1z"/></svg>
    </li>
    <li class="contact-item">
      <span>marla@valcorne.com</span>
      <svg class="contact-icon" viewBox="0 0 24 24" aria-hidden="true"><rect x="2" y="5" width="20" height="14" rx="1" fill="#fff"/><path d="M3 6l9 7 9-7" fill="none" stroke="#a41c22" stroke-width="1.8"/></svg>
    </li>
    <li class="contact-item">
      <span>valcorne.com</span>
      <svg class="contact-icon" viewBox="0 0 24 24" aria-hidden="true"><circle cx="12" cy="12" r="10" fill="#fff"/><path d="M2 12h20M12 2c3 3 3 17 0 20M12 2c-3 3-3 17 0 20" fill="none" stroke="#a41c22" stroke-width="1.5"/></svg>
    </li>
  </ul>
</section>

<section class="card card-back">
  <div class="back-decoration" role="img" aria-label="Faint large brand decoration area"></div>
  <div class="back-mark" aria-hidden="true"></div>
  <div class="back-brand">
    <div class="brand-name">VALCORNE</div>
    <div class="brand-rule"></div>
    <div class="brand-tag">HEALTH CARE MARKETING</div>
  </div>
</section>

</body>
</html>
```